Website design for legal tech start up in Switzerland (B2B)

We are for a legal tech start up in Switzerland called KOVA. We have been running since August 2016. This will be our first live website.

We need a website designed and business card design for our start-up in Switzerland. We also need the Web design to be converted into HTML and CSS files.

Function of website:
• To inform potential customers of our services
• Form a key part of our digital marketing and sales footprint.
• Branding

Please find attached logo.
Updates

Project Deadline Extended Reason: Giving us time to review submissions and provide opportunity for more submissions. Added Thursday, February 16, 2017

Project Deadline Extended
Reason: Looking for more idea's not necessarily set on blue and grey colours only.

Target Market(s)

B2B tech powered legal services.

Industry/Entity Type

Legal

Contact Information for Business Card

Lean and slick design.

Coding

Coded - Design and coding required

Number of Pages Required

5+ page

Requirements
Must have
• VERY LEAN AND CLEAN DESIGN!
• We have received many great standard designs, but we are looking for something more out-of-the box: You can get inspiration from these designs: http://www.pixelvane.com/websites/clean/
• Thanks!!
• Easy content management system
• Well structured coding for additional development
• Responsive webpage for all types of devices
• SEO optimized
• Tabs (Home, services, team, careers, blog, contact us)
• Colour scheme complementary to logo
Nice to have
• Look and Design - Approachable, High-tech, Modern
• Easy to add chat bot capability in future
Should not have
• Too busy/ too much clutter
• Not take to long to load

```html
<!DOCTYPE html>
<html lang="en">
<head>
<meta charset="utf-8">
<title>KOVA – Legal Startup Company</title>
<link rel="stylesheet" href="https://fonts.googleapis.com/css2?family=Lato:wght@400;700;900&family=Open+Sans:ital,wght@0,400;0,600;0,700;1,400&display=swap">
<style>
:root{
  --navy:#1b2f5e;
  --ink:#333639;
  --muted:#77797c;
  --line:#cfd3d8;
  --band:#eef1f6;
  --dark-band:#444546;
  --white:#ffffff;
  --heading-font:'Lato',sans-serif;
  --body-font:'Open Sans',sans-serif;
}
*{box-sizing:border-box;margin:0;padding:0}
html,body{width:1200px;height:2727px;overflow:hidden;background:var(--white)}
body{position:relative;font-family:var(--body-font);color:var(--ink)}
.abs{position:absolute}

/* header */
.brand{left:100px;top:22px;font-family:var(--heading-font);font-weight:900;font-size:44px;letter-spacing:3px;color:var(--ink);line-height:1}
.top-contact{top:14px;right:100px;display:flex;gap:30px;align-items:center;font-size:15px;font-weight:600}
.top-contact span{display:flex;align-items:center;gap:10px}
.round-icon{width:30px;height:30px;border:1px solid #9aa0a8;border-radius:50%;display:flex;align-items:center;justify-content:center}
.main-nav{top:58px;right:100px;display:flex;gap:27px;font-family:var(--heading-font);font-weight:700;font-size:15px;color:var(--ink);align-items:center}
.main-nav .active{color:var(--navy)}

/* hero */
.hero{left:0;top:90px;width:1200px;height:472px;background:radial-gradient(ellipse at 30% 90%,#a8652a 0%,rgba(120,80,40,0) 35%),radial-gradient(ellipse at 75% 80%,#6a5538 0%,rgba(0,0,0,0) 40%),linear-gradient(180deg,#2b3f5e 0%,#1e2d44 35%,#2c3346 65%,#3a3328 100%)}
.hero-title{top:212px;width:1200px;text-align:center;font-family:var(--heading-font);font-weight:900;font-size:60px;color:var(--white);letter-spacing:.5px}
.hero-sub{top:286px;width:1200px;text-align:center;font-size:21px;line-height:33px;color:var(--white)}
.hero-btn{left:505px;top:378px;width:190px;height:40px;border:2px solid var(--white);border-radius:20px;background:var(--navy);color:var(--white);font-family:var(--heading-font);font-weight:700;font-size:14px;display:flex;align-items:center;justify-content:center}
.dots{top:496px;left:562px;display:flex;gap:5px}
.dots i{width:14px;height:14px;border:2px solid var(--white);border-radius:50%}
.dots i.on{background:var(--white)}

/* section headings */
.section-title{width:1200px;text-align:center;font-family:var(--heading-font);font-weight:700;font-size:31px;color:var(--ink)}
.lead{width:1200px;text-align:center;font-size:12.5px;line-height:24px;color:var(--muted)}

/* welcome features */
.feature{width:250px;text-align:center}
.feature .ring{width:142px;height:142px;margin:0 auto;border:1.5px solid #8d9198;border-radius:50%;display:flex;align-items:center;justify-content:center}
.feature h3{margin-top:36px;font-family:var(--heading-font);font-weight:700;font-size:18px;color:var(--ink)}
.feature p{margin-top:10px;font-size:12.5px;line-height:22px;color:var(--muted)}
.feature .more{margin-top:12px;font-family:var(--heading-font);font-weight:900;font-size:13px;color:var(--navy)}

/* what we do */
.what{left:0;top:1093px;width:1200px;height:400px;background:var(--band)}
.what h2{left:100px;top:50px;font-family:var(--heading-font);font-weight:700;font-size:31px}
.what .copy{left:100px;top:105px;width:460px;font-size:12.5px;line-height:26px;color:var(--muted)}
.what .copy p+p{margin-top:18px}
.pill{height:34px;border:1.5px solid #8d9198;border-radius:17px;font-family:var(--heading-font);font-weight:900;font-size:12.5px;color:var(--navy);display:flex;align-items:center;justify-content:center;width:136px;background:transparent}
.video{left:605px;top:56px;width:495px;height:285px;border:4px solid var(--white);box-shadow:0 0 0 1px #d5d8dc;background:linear-gradient(120deg,#3a4252 0%,#c9c6c2 40%,#e8e3dc 60%,#8a8480 100%)}
.play{left:806px;top:1253px}

/* columns */
.col{width:313px}
.col h2{font-family:var(--heading-font);font-weight:700;font-size:26px;color:var(--ink);padding-bottom:12px;border-bottom:4px solid var(--ink)}
.col.accent h2{border-bottom-color:var(--navy)}
.col .photo{margin-top:23px;height:182px;border:3px solid var(--white);box-shadow:0 0 0 1px #d5d8dc}
.col p{margin-top:22px;font-size:12.5px;line-height:24px;color:var(--muted)}
.col .pill{margin-top:24px}

/* testimonial */
.quote-band{left:0;top:2016px;width:1200px;height:209px;background:var(--dark-band)}
.avatar{left:115px;top:42px;width:125px;height:125px;border-radius:50%;border:4px solid var(--white);background:radial-gradient(circle at 50% 40%,#c79c85 0%,#8c6a5a 45%,#3a5f8a 100%)}
.divider{left:271px;top:40px;width:1px;height:125px;background:#8a8b8c}
.quote{left:304px;top:44px;width:800px;font-style:italic;font-size:14.5px;line-height:27px;color:#e8e8e8}
.quote-author{left:306px;top:138px;font-family:var(--heading-font);font-weight:700;font-size:19px;color:var(--white)}
.arrow{top:88px}

/* contact */
.contact-sub{font-family:var(--heading-font);font-weight:700;font-size:19px;color:var(--ink)}
.field{height:31px;border:1px solid #b9bdc3;font-size:12px;color:#666;padding:8px 10px}
.submit{left:625px;top:2580px;width:79px;height:28px;border:1.5px solid #8d9198;border-radius:14px;font-family:var(--heading-font);font-weight:900;font-size:12px;display:flex;align-items:center;justify-content:center}
.info-row{left:782px;display:flex;gap:24px;align-items:flex-start;font-size:12.5px;line-height:26px;color:var(--muted)}
.social{left:782px;top:2577px;display:flex;gap:6px}
.social i{width:28px;height:28px;border-radius:50%}
.footer-line{left:100px;top:2649px;width:1000px;height:1px;background:var(--line)}
.copyright{top:2676px;width:1200px;text-align:center;font-size:12px;color:var(--muted)}
</style>
</head>
<body>

<header>
  <div class="abs brand">KOVA</div>
  <div class="abs top-contact">
    <span><i class="round-icon"><svg width="14" height="14" viewBox="0 0 24 24"><path fill="#1b2f5e" d="M6.6 10.8a15 15 0 0 0 6.6 6.6l2.2-2.2c.3-.3.7-.4 1-.2 1.1.4 2.3.6 3.6.6.6 0 1 .4 1 1V20c0 .6-.4 1-1 1A17 17 0 0 1 3 4c0-.6.4-1 1-1h3.5c.6 0 1 .4 1 1 0 1.3.2 2.5.6 3.6.1.3 0 .7-.2 1z"/></svg></i>1 555 204 7730</span>
    <span><i class="round-icon"><svg width="14" height="14" viewBox="0 0 24 24"><path fill="#1b2f5e" d="M2 5h20v14H2zm2 2v.5l8 5 8-5V7z"/></svg></i>info@kova.com</span>
  </div>
  <nav class="abs main-nav">
    <span class="active">HOME</span><span>SERVICES</span><span>TEAM</span><span>CAREERS</span><span>BLOG</span><span>CONTACT US</span>
    <svg width="14" height="14" viewBox="0 0 24 24"><circle cx="10" cy="10" r="6.5" fill="none" stroke="#333639" stroke-width="3"/><path d="M15 15l6 6" stroke="#333639" stroke-width="3.5"/></svg>
  </nav>
</header>

<section class="abs hero" role="img" aria-label="Aerial photo of a city at dusk with glowing streets"></section>
<h1 class="abs hero-title">LEGAL STARTUP COMPANY</h1>
<p class="abs hero-sub">At vero eos et accusamus et iusto odio dignissimos ducimus qui<br>blan ditiis praesentium voluptatum deleniti atque corru</p>
<div class="abs hero-btn">GET MORE INFO</div>
<div class="abs dots"><i class="on"></i><i></i><i></i><i></i></div>

<h2 class="abs section-title" style="top:616px">WELCOME TO KOVA</h2>
<p class="abs lead" style="top:676px">At vero eos et accusamus et iusto odio dignissimos ducimus qui blanditiis praesentium voluptatum deleniti atque corrupti quos dolores<br>et quas molestias excepturi sint occaecati cupiditate milique sunt in culpa qui officia deserunt mollitia animi, id est</p>

<div class="abs feature" style="left:86px;top:760px">
  <div class="ring"><svg width="60" height="60" viewBox="0 0 60 60"><path d="M26 6 8 12v14c0 13 8 22 18 26 3-1 6-3 8-5" fill="none" stroke="#1b2f5e" stroke-width="4"/><path d="M26 14 15 18v8c0 8 5 14 11 17" fill="#1b2f5e"/><circle cx="42" cy="30" r="12" fill="#1b2f5e"/><path d="m36 30 4 4 8-8" fill="none" stroke="#fff" stroke-width="3"/></svg></div>
  <h3>Confidential</h3><p>Nam libero tempore, cum soluta no bis<br>est eligendi optio cumque nihili</p><div class="more">READ MORE &gt;&gt;</div>
</div>
<div class="abs feature" style="left:344px;top:760px">
  <div class="ring"><svg width="62" height="62" viewBox="0 0 62 62"><rect x="6" y="8" width="50" height="44" fill="none" stroke="#1b2f5e" stroke-width="3"/><rect x="6" y="8" width="50" height="9" fill="#1b2f5e"/><g fill="#1b2f5e"><rect x="12" y="22" width="6" height="5"/><rect x="22" y="22" width="6" height="5"/><rect x="32" y="22" width="6" height="5"/><rect x="42" y="22" width="6" height="5"/><rect x="22" y="31" width="6" height="5"/><rect x="32" y="31" width="6" height="5"/><rect x="42" y="31" width="6" height="5"/><rect x="32" y="40" width="6" height="5"/><rect x="42" y="40" width="6" height="5"/></g><circle cx="16" cy="44" r="9" fill="#fff" stroke="#1b2f5e" stroke-width="3"/><path d="M16 39v5h4" fill="none" stroke="#1b2f5e" stroke-width="2"/></svg></div>
  <h3>Development &amp; Planning</h3><p>Nam libero tempore, cum soluta no bis<br>est eligendi optio cumque nihili</p><div class="more">READ MORE &gt;&gt;</div>
</div>
<div class="abs feature" style="left:606px;top:760px">
  <div class="ring"><svg width="64" height="60" viewBox="0 0 64 60"><rect x="24" y="6" width="16" height="10" fill="none" stroke="#1b2f5e" stroke-width="3"/><rect x="4" y="14" width="56" height="38" fill="#1b2f5e"/><rect x="10" y="24" width="18" height="20" fill="#fff"/><circle cx="19" cy="31" r="4" fill="#1b2f5e"/><path d="M12 43c1-6 13-6 14 0z" fill="#1b2f5e"/><rect x="33" y="26" width="21" height="3" fill="#fff"/><rect x="33" y="33" width="21" height="3" fill="#fff"/><rect x="33" y="40" width="14" height="3" fill="#fff"/></svg></div>
  <h3>Corporate &amp; Insolvency</h3><p>Nam libero tempore, cum soluta no bis<br>est eligendi optio cumque nihili</p><div class="more">READ MORE &gt;&gt;</div>
</div>
<div class="abs feature" style="left:864px;top:760px">
  <div class="ring"><svg width="56" height="62" viewBox="0 0 56 62"><rect x="12" y="4" width="38" height="48" fill="#fff" stroke="#1b2f5e" stroke-width="3"/><rect x="5" y="11" width="38" height="48" fill="#fff" stroke="#1b2f5e" stroke-width="3"/><g fill="#1b2f5e"><rect x="11" y="18" width="26" height="3"/><rect x="11" y="26" width="12" height="3"/><rect x="11" y="33" width="12" height="3"/><rect x="11" y="40" width="12" height="3"/><rect x="11" y="48" width="26" height="3"/></g><text x="31" y="43" font-family="Lato,sans-serif" font-weight="900" font-size="18" fill="#1b2f5e" text-anchor="middle">$</text></svg></div>
  <h3>Commercial Litigation</h3><p>Nam libero tempore, cum soluta no bis<br>est eligendi optio cumque nihili</p><div class="more">READ MORE &gt;&gt;</div>
</div>

<section class="abs what">
  <h2 class="abs">WHAT WE DO</h2>
  <div class="abs copy">
    <p>At vero eos et accusamus et iusto odio dignissimos ducimus qui blanditiis prasent ium voluptatum deleniti atque corrupti quo.</p>
    <p>Dolores et quas molestias excepturi sint occaecati cupiditate non provident similiq ue sunt in culpa qui officia deserunt mollitia animi, id est laborum et dolorum fug t harum quidem rerum facilis est et expedita voluptas assumenda est, omnis dolorr epellend poribus autem quibusdam et aut officiis.</p>
  </div>
  <div class="abs pill" style="left:100px;top:321px">READ MORE &gt;&gt;</div>
  <div class="abs video" role="img" aria-label="Video still of hands signing a contract at a desk"></div>
</section>
<svg class="abs play" width="64" height="64" viewBox="0 0 64 64"><circle cx="32" cy="32" r="31" fill="#2a2a2a"/><path d="M25 19v26l21-13z" fill="#fff"/></svg>

<article class="abs col" style="left:100px;top:1550px">
  <h2>EXPERTISE</h2>
  <div class="photo" role="img" aria-label="Photo of hands typing on a laptop" style="background:linear-gradient(135deg,#f3f3f3 0%,#9a9ea6 45%,#5c5f66 70%,#e9e6e3 100%)"></div>
  <p>Nam libero tempore, cum soluta nobis est eligen optioc umque nihil impedit quo minus id quod maxime placat facere possimus omnis volupta.</p>
  <div class="pill">READ MORE &gt;&gt;</div>
</article>
<article class="abs col accent" style="left:444px;top:1550px">
  <h2>CAREERS</h2>
  <div class="photo" role="img" aria-label="Photo of a businessman in a café holding a tablet" style="background:linear-gradient(90deg,#4a4f3a 0%,#c99a55 35%,#2e3a50 55%,#d8b070 100%)"></div>
  <p>Nam libero tempore, cum soluta nobis est eligen optioc umque nihil impedit quo minus id quod maxime placat facere possimus omnis volupta.</p>
  <div class="pill">READ MORE &gt;&gt;</div>
</article>
<article class="abs col" style="left:787px;top:1550px">
  <h2>NEWSROOM</h2>
  <div class="photo" role="img" aria-label="Photo of a team meeting silhouetted against an office window" style="background:linear-gradient(180deg,#2f7d8c 0%,#8fc7c9 40%,#e6b26a 65%,#5a4a3e 100%)"></div>
  <p>Nam libero tempore, cum soluta nobis est eligen optioc umque nihil impedit quo minus id quod maxime placat facere possimus omnis volupta.</p>
  <div class="pill">READ MORE &gt;&gt;</div>
</article>

<section class="abs quote-band">
  <div class="abs avatar" role="img" aria-label="Portrait photo of the client quoted"></div>
  <div class="abs divider"></div>
  <p class="abs quote">Nam libero tempore, cum soluta nobis est eligendi optio cumque nihil impedit quo minus id quod maxime placeat facere possimus, omnis voluptas assumenda est, omnis dolor repellendus. Temporibus autem quibusdam et aut officiis debitis aut rerum necessitatibus saepe eveniet ut et voluptates repudiandae sint et molestiae</p>
  <div class="abs quote-author">- Mathis Dorsaz</div>
  <svg class="abs arrow" style="left:34px" width="20" height="32" viewBox="0 0 20 32"><path d="M16 3 4 16l12 13" fill="none" stroke="#bdbdbd" stroke-width="3"/></svg>
  <svg class="abs arrow" style="left:1145px" width="20" height="32" viewBox="0 0 20 32"><path d="M4 3l12 13L4 29" fill="none" stroke="#bdbdbd" stroke-width="3"/></svg>
</section>

<h2 class="abs section-title" style="top:2287px">CONTACT US</h2>
<h3 class="abs contact-sub" style="left:98px;top:2360px">Get In Touch:</h3>
<div class="abs field" style="left:100px;top:2409px;width:295px">Name :</div>
<div class="abs field" style="left:407px;top:2409px;width:297px">Phone :</div>
<div class="abs field" style="left:100px;top:2451px;width:604px">Email :</div>
<div class="abs field" style="left:100px;top:2494px;width:604px;height:72px">Message :</div>
<div class="abs submit">SUBMIT</div>

<h3 class="abs contact-sub" style="left:782px;top:2360px">Contact Information</h3>
<div class="abs info-row" style="top:2408px"><i class="round-icon"><svg width="12" height="14" viewBox="0 0 24 28"><path fill="#1b2f5e" d="M12 0a10 10 0 0 0-10 10c0 8 10 18 10 18s10-10 10-18A10 10 0 0 0 12 0zm0 14a4 4 0 1 1 0-8 4 4 0 0 1 0 8z"/></svg></i><span>14 Lindenweg, 3rd Floor<br>Switzerland 8004</span></div>
<div class="abs info-row" style="top:2468px"><i class="round-icon"><svg width="14" height="14" viewBox="0 0 24 24"><path fill="#1b2f5e" d="M6.6 10.8a15 15 0 0 0 6.6 6.6l2.2-2.2c.3-.3.7-.4 1-.2 1.1.4 2.3.6 3.6.6.6 0 1 .4 1 1V20c0 .6-.4 1-1 1A17 17 0 0 1 3 4c0-.6.4-1 1-1h3.5c.6 0 1 .4 1 1 0 1.3.2 2.5.6 3.6.1.3 0 .7-.2 1z"/></svg></i><span>1 555 204 7730</span></div>
<div class="abs info-row" style="top:2522px"><i class="round-icon"><svg width="14" height="14" viewBox="0 0 24 24"><path fill="#1b2f5e" d="M2 5h20v14H2zm2 2v.5l8 5 8-5V7z"/></svg></i><span>info@kova.com</span></div>
<div class="abs social"><i style="background:#1b2f5e"></i><i style="background:#2aa3e0"></i><i style="background:#e03a32"></i><i style="background:#b8865a"></i></div>

<div class="abs footer-line"></div>
<footer class="abs copyright">Copyrights © 2017, Kova. All Rights Reserved.</footer>

</body>
</html>
```